Dental specialist needs a sharp looking letterhead

I am looking for a letterhead to be used to send letters and communication between myself (a dental specialist) and other dentists.
My office is a state of the art dental specialty office.
I need to letterhead to also state:
Bertram L. Oswick DDS
2748 Tollard Avenue, Suite K
West Tollard, NY 14391
(716)392-5061
fax: (716)392-5087
oswickroot.com (**this email address may change)

i included my logo designs.
thank you

Target Market(s)

dentists

Industry/Entity Type

Communication

Requirements
Must have
• the included logo, whether the vertical or horizontal versions

```html
<!DOCTYPE html>
<html lang="en">
<head>
<meta charset="utf-8">
<title>Meridian Endodontics P.C. Letterhead</title>
<link rel="stylesheet" href="https://fonts.googleapis.com/css2?family=Arimo&family=Merriweather:wght@700&display=swap">
<style>
  :root {
    --ink: #111111;
    --text-grey: #333333;
    --brand-blue: #42a1d8;
    --paper: #ffffff;
  }
  html, body {
    margin: 0;
    padding: 0;
    overflow: hidden;
    background: var(--paper);
  }
  .letterhead {
    position: relative;
    width: 931px;
    height: 1200px;
    background: var(--paper);
    overflow: hidden;
    font-family: "Arimo", Arial, sans-serif;
  }
  .brand-mark {
    position: absolute;
    left: 34px;
    top: 36px;
    width: 70px;
    height: 70px;
    border-radius: 50%;
    background: var(--brand-blue);
  }
  .brand-divider {
    position: absolute;
    left: 118px;
    top: 20px;
    width: 1px;
    height: 93px;
    background: var(--ink);
  }
  .brand-name {
    position: absolute;
    left: 127px;
    top: 42px;
    margin: 0;
    font-family: "Merriweather", Georgia, serif;
    font-weight: 700;
    color: var(--ink);
    line-height: 1;
  }
  .brand-name .primary {
    display: block;
    font-size: 30px;
    letter-spacing: -0.5px;
  }
  .brand-name .secondary {
    display: block;
    margin-top: 8px;
    font-size: 13px;
    letter-spacing: 2px;
    padding-left: 26px;
  }
  .doctor-contact {
    position: absolute;
    right: 36px;
    top: 28px;
    text-align: right;
    color: var(--text-grey);
  }
  .doctor-name {
    margin: 0 0 8px;
    font-size: 20px;
    font-weight: 400;
  }
  .contact-line {
    margin: 0 0 5px;
    font-size: 15px;
    display: flex;
    align-items: center;
    justify-content: flex-end;
    gap: 5px;
  }
  .contact-line svg { fill: var(--brand-blue); }
  .footer-wave {
    position: absolute;
    left: 0;
    top: 1090px;
    width: 931px;
    height: 110px;
  }
  .wave-black { fill: var(--ink); }
  .wave-blue { fill: var(--brand-blue); }
  .office-details {
    position: absolute;
    left: 58px;
    top: 1136px;
    color: var(--paper);
    font-size: 17px;
  }
  .office-details p {
    margin: 0 0 11px;
    display: flex;
    align-items: center;
    gap: 6px;
  }
  .office-details svg { fill: var(--paper); }
</style>
</head>
<body>
<main class="letterhead">
  <header>
    <div class="brand-mark"></div>
    <div class="brand-divider"></div>
    <h1 class="brand-name">
      <span class="primary">MERIDIAN</span>
      <span class="secondary">Endodontics P.C.</span>
    </h1>
    <address class="doctor-contact">
      <p class="doctor-name">Bertram L. Oswick, DDS</p>
      <p class="contact-line">
        <svg width="13" height="13" viewBox="0 0 24 24" aria-hidden="true"><path d="M6.6 10.8a15.1 15.1 0 0 0 6.6 6.6l2.2-2.2c.3-.3.7-.4 1-.2 1.1.4 2.3.6 3.6.6.6 0 1 .4 1 1V20c0 .6-.4 1-1 1A17 17 0 0 1 3 4c0-.6.4-1 1-1h3.5c.6 0 1 .4 1 1 0 1.3.2 2.5.6 3.6.1.3 0 .7-.2 1z"/></svg>
        (716)392-5061
      </p>
      <p class="contact-line">
        <svg width="14" height="10" viewBox="0 0 24 16" aria-hidden="true"><path d="M0 0h24v16H0z M2 2l10 7 10-7" fill-rule="evenodd"/><path d="M1 1l11 8 11-8" stroke="#fff" stroke-width="1.6" fill="none"/></svg>
        oswickendo@mailbox.com
      </p>
    </address>
  </header>

  <footer>
    <svg class="footer-wave" viewBox="0 0 931 110" aria-hidden="true">
      <path class="wave-black" d="M0 34 Q460 -10 931 62 L931 86 Q470 14 0 38 Z"/>
      <path class="wave-blue" d="M0 42 Q470 18 931 92 L931 110 L0 110 Z"/>
    </svg>
    <address class="office-details">
      <p>
        <svg width="16" height="14" viewBox="0 0 24 20" aria-hidden="true"><path d="M6 0h10l2 2v4H6z M2 7h20c1 0 2 1 2 2v8H0V9c0-1 1-2 2-2z M6 15h12v5H6z"/></svg>
        (716)392-5087
      </p>
      <p>
        <svg width="14" height="18" viewBox="0 0 24 32" aria-hidden="true"><path d="M12 0a12 12 0 0 0-12 12c0 9 12 20 12 20s12-11 12-20A12 12 0 0 0 12 0zm0 17a5 5 0 1 1 0-10 5 5 0 0 1 0 10z"/></svg>
        2748 Tollard Avenue, Suite K, West Tollard, NY 14391
      </p>
    </address>
  </footer>
</main>
</body>
</html>
```